I need a business card design for a new business based in South West Australia.
I specialize in residential window cleaning & general handyman maintenance.

Dale Marsh - 412 SILVER HAWK DETAILING
- Window Cleaning
- House Maintenance

```html
<!DOCTYPE html>
<html lang="en">
<head>
<meta charset="utf-8">
<title>412 Silver Hawk Detailing – Business Card</title>
<link rel="stylesheet" href="https://fonts.googleapis.com/css2?family=Open+Sans:wght@400;600&display=swap">
<style>
  :root {
    --backdrop: #e9e6e1;
    --card-dark: #2b2b2c;
    --card-dark-edge: #1c1c1d;
    --panel-white: #f6f6f6;
    --panel-shade: #dcdcdc;
    --band-grey: #a9a9aa;
    --text-light: #f2f2f2;
    --text-soft: #d9d9d9;
    --art-red: #d94a50;
    --art-grey: #e4e4e4;
  }
  html, body {
    margin: 0;
    width: 1200px;
    height: 892px;
    overflow: hidden;
    background: var(--backdrop);
  }
  .canvas {
    position: relative;
    width: 1200px;
    height: 892px;
  }
  .card {
    position: absolute;
    left: 150px;
    top: 189px;
    width: 900px;
    height: 514px;
    background: linear-gradient(160deg, var(--card-dark) 0%, var(--card-dark-edge) 100%);
    border-radius: 6px;
    overflow: hidden;
    box-shadow: 0 18px 40px rgba(0,0,0,0.25);
    font-family: "Open Sans", Arial, sans-serif;
  }
  .card-curve {
    position: absolute;
    inset: 0;
  }
  .company-name {
    position: absolute;
    left: 60px;
    top: 52px;
    margin: 0;
    color: var(--text-light);
    font-size: 40px;
    font-weight: 400;
    letter-spacing: 0.5px;
  }
  .owner-name {
    position: absolute;
    right: 70px;
    top: 118px;
    margin: 0;
    color: var(--text-light);
    font-size: 34px;
    font-weight: 600;
  }
  .services {
    position: absolute;
    right: 40px;
    top: 178px;
    margin: 0;
    padding: 0;
    list-style: none;
    text-align: right;
  }
  .services li {
    color: var(--text-soft);
    font-size: 24px;
    line-height: 38px;
  }
  .services li::after {
    content: "";
    display: inline-block;
    width: 10px;
    height: 10px;
    margin-left: 16px;
    border-radius: 50%;
    background: var(--text-soft);
    vertical-align: middle;
  }
  .services li:first-child { margin-right: 36px; }
  .service-art {
    position: absolute;
    left: 210px;
    top: 300px;
    width: 270px;
    height: 190px;
    border-radius: 10px;
    background: radial-gradient(circle at 55% 35%, var(--art-red) 0 22%, var(--art-grey) 48%, var(--panel-white) 75%);
  }
</style>
</head>
<body>
  <main class="canvas">
    <section class="card">
      <svg class="card-curve" width="900" height="514" viewBox="0 0 900 514" aria-hidden="true">
        <path d="M0,262 Q540,150 900,514 L0,514 Z" fill="var(--band-grey)"/>
        <path d="M0,282 Q540,175 900,514 L0,514 Z" fill="var(--panel-shade)"/>
        <path d="M0,296 Q540,192 880,514 L0,514 Z" fill="var(--panel-white)"/>
      </svg>
      <h1 class="company-name">412 SILVER HAWK DETAILING</h1>
      <p class="owner-name">Dale Marsh</p>
      <ul class="services">
        <li>Window Cleaning</li>
        <li>House Maintenance</li>
      </ul>
      <div class="service-art" role="img" aria-label="Illustration of a handyman with a hammer beside a small house with a red roof"></div>
    </section>
  </main>
</body>
</html>
```